Business Card Design - Photographer

I am a landscape photographer and I require a business card design. 

I require two designs:
1)  a double sided business card
 and
b)  a single sided business card 

The single sided design can either be the same as the double sided (with just one side having all the information)....or it can be an entire new design. Its up to you.

My corporate colours are (CMYK):

Blue   69, 32, 0, 0
Grey  72,  64,  47,  31
Green  32,  2,  91,  0
Yellow   0, 19, 92, 0
Orange  0, 39, 75, 0

Colour space in final file should be in CMYK.

The details that need to be included on the card:

- Use the provided Logo
- Name: Wiktor Baranowski
- Email:   sales@vistalumeworks.com.au
- Website:    vistalumeworks.com.au
- Twitter:    twitter.com/vistalumeworks
- Facebook:   facebook.com/vistalumeworks
- Mobile  0417 539 662

Please use the attached template to design the logo to the specified size, including the marked bleed lines. I have also attached my logo in PNG (transparent background) and ai format for you to use.

The final file should be:
- Photoshop version with layers so I can edit the name/text etc. All non vector files should be high resolution at 1039 x 697 pixels at 300 dpi.

I also require a file as:
- Vector based PDF

Anyway questions please contact me.

Thank you

Industry/Entity Type

Landscape

Logo styles of interest
Pictorial/Combination Logo
Abstract Logo
Wordmark Logo
Lettermark Logo
Requirements
Must have
• The details that need to be included on the card:

- Use the provided Logo
- Name: Wiktor Baranowski
- Email: sales@vistalumeworks.com.au
- Website: vistalumeworks.com.au
- Twitter: twitter.com/vistalumeworks
- Facebook: facebook.com/vistalumeworks
- Mobile 0417 539 662

```html
<!DOCTYPE html>
<html lang="en">
<head>
<meta charset="UTF-8">
<title>Vistalume Works – Business Card</title>
<link href="https://fonts.googleapis.com/css2?family=Cinzel:wght@400&family=Tinos&family=Open+Sans:wght@400&display=swap" rel="stylesheet">
<style>
  :root {
    --page: #efeae4;
    --card: #ffffff;
    --blue: #3e8ccc;
    --navy: #3b3f56;
    --yellow: #fcc512;
    --ink: #3b3f56;
    --white: #ffffff;
    --social: #6d7388;
  }
  * { margin: 0; padding: 0; box-sizing: border-box; }
  html, body { width: 1200px; height: 1100px; overflow: hidden; background: var(--page); }
  .canvas { position: relative; width: 1200px; height: 1100px; }

  .card {
    position: absolute;
    width: 760px;
    height: 434px;
    overflow: hidden;
    box-shadow: 0 6px 18px rgba(0,0,0,0.18);
  }
  .card--front { left: 70px; top: 70px; background: var(--card); }
  .card--back  { left: 297px; top: 552px; background: var(--blue); }

  .card__waves { position: absolute; inset: 0; width: 100%; height: 100%; }

  .brand-mark {
    position: absolute;
    border-radius: 50%;
    background: var(--navy);
  }
  .card--front .brand-mark { width: 100px; height: 100px; left: 196px; top: 30px; }
  .card--back  .brand-mark { width: 120px; height: 120px; left: 320px; top: 88px; }

  .brand-name {
    position: absolute;
    font-family: "Cinzel", serif;
    font-weight: 400;
    color: var(--ink);
    white-space: nowrap;
  }
  .card--front .brand-name { left: 83px; top: 146px; font-size: 34px; letter-spacing: 0.5px; }
  .card--back  .brand-name { left: 0; width: 760px; text-align: center; top: 232px; font-size: 42px; letter-spacing: 0.5px; }

  .contact-list {
    position: absolute;
    left: 84px;
    top: 246px;
    list-style: none;
    font-family: "Tinos", serif;
    font-size: 19px;
    color: var(--ink);
  }
  .contact-list li { display: flex; align-items: center; height: 26.5px; }
  .contact-list svg, .contact-list .social-dot { flex: none; width: 13px; height: 13px; margin-right: 7px; }
  .social-dot { display: inline-block; background: var(--social); border-radius: 2px; }

  .address {
    position: absolute;
    right: 40px;
    top: 360px;
    text-align: right;
    font-family: "Tinos", serif;
    font-size: 19px;
    line-height: 26px;
    color: var(--white);
  }

  .back-url {
    position: absolute;
    left: 0;
    width: 760px;
    top: 352px;
    text-align: center;
    font-family: "Open Sans", sans-serif;
    font-size: 19px;
    letter-spacing: 3px;
    color: var(--white);
  }
</style>
</head>
<body>
<main class="canvas">

  <section class="card card--front" aria-label="Business card front">
    <svg class="card__waves" viewBox="0 0 525 300" preserveAspectRatio="none" aria-hidden="true">
      <path fill="var(--blue)" d="M215,300 C340,272 440,228 525,196 L525,300 Z"/>
      <path fill="var(--yellow)" d="M0,262 C70,290 160,296 240,287 C360,273 450,218 525,180 L525,170 C440,210 350,262 230,278 C150,288 70,282 0,250 Z"/>
      <path fill="var(--yellow)" d="M0,268 C60,290 130,294 170,293 C110,298 50,296 0,290 Z"/>
      <path fill="var(--navy)" d="M0,228 C40,262 110,282 200,287 C120,293 50,282 0,262 Z"/>
      <path fill="var(--navy)" d="M430,244 C460,222 495,200 525,182 L525,146 C490,178 460,212 430,244 Z"/>
    </svg>

    <div class="brand-mark" aria-hidden="true"></div>
    <h1 class="brand-name">Vistalume Works</h1>

    <ul class="contact-list">
      <li>
        <svg viewBox="0 0 13 13" aria-hidden="true"><rect x="3.5" y="1" width="6" height="11" rx="1" fill="var(--ink)"/><rect x="4.5" y="2.5" width="4" height="6" fill="#fff"/></svg>
        0417 539 662
      </li>
      <li>
        <svg viewBox="0 0 13 13" aria-hidden="true"><rect x="1" y="3" width="11" height="7" fill="var(--ink)"/><path d="M1,3 L6.5,7 L12,3" stroke="#fff" stroke-width="1" fill="none"/></svg>
        sales@vistalumeworks.com.au
      </li>
      <li>
        <svg viewBox="0 0 13 13" aria-hidden="true"><circle cx="6.5" cy="6.5" r="5" fill="var(--ink)"/><path d="M1.5,6.5 H11.5 M6.5,1.5 V11.5" stroke="#fff" stroke-width="0.8"/></svg>
        www.vistalumeworks.com.au
      </li>
      <li><span class="social-dot" aria-hidden="true"></span>vistalumeworks</li>
      <li><span class="social-dot" aria-hidden="true"></span>vistalumeworks</li>
    </ul>

    <p class="address">00, Complex Name<br>State Name, City 0020</p>
  </section>

  <section class="card card--back" aria-label="Business card back">
    <div class="brand-mark" aria-hidden="true"></div>
    <h2 class="brand-name">Vistalume Works</h2>
    <p class="back-url">www.vistalumeworks.com.au</p>
  </section>

</main>
</body>
</html>
```